Kellwyn Surface Records

I have a current web site that it looking quite aged and it needs a new lease of life. This is a Graffiti Management Website so is all about data processing and management of information. I want a html 5 view on any platform design. clean crisp and new. I have provided some screen shots of my current site.

Target Market(s)

The Target Market will be local government. most users will not be heavy pc users

Industry/Entity Type

Management

Font styles to use
Sans Serif
Other font styles liked:
• web font like calibri

Colors

Designer to choose colors to be used in the design.

Requirements
Must have
• Must have menus similar to attachments

```html
<!DOCTYPE html>
<html lang="en">
<head>
<meta charset="utf-8">
<title>Kellwyn Surface Records</title>
<link href="https://fonts.googleapis.com/css2?family=Carlito:wght@400;700&display=swap" rel="stylesheet">
<style>
:root{
  --blue:#3f9fd6;
  --blue-dark:#0e1a78;
  --header-stripe:#5aa6de;
  --header-stripe-light:#79bbe8;
  --ink:#2c2c2c;
  --text:#5a5a5a;
  --muted:#888;
  --rule:#d6d6d6;
  --footer:#0b0b0b;
  --white:#fff;
}
*{margin:0;padding:0;box-sizing:border-box}
html,body{width:859px;height:1200px;overflow:hidden;background:var(--white)}
body{font-family:"Carlito",Calibri,Arial,sans-serif;color:var(--text);position:relative}
.abs{position:absolute}

.site-header{left:0;top:0;width:859px;height:68px;
  background:repeating-linear-gradient(180deg,var(--header-stripe) 0 2px,var(--header-stripe-light) 2px 4px);}
.site-header .top-edge{left:0;top:0;width:859px;height:3px;background:var(--blue-dark)}
.site-header .tag-band{left:0;top:52px;width:859px;height:14px;background:var(--blue-dark)}
.brand{left:102px;top:8px;font-size:34px;font-weight:700;letter-spacing:18px;color:var(--white)}
.tagline{left:103px;top:53px;font-size:11px;font-weight:700;letter-spacing:1.6px;color:var(--white);text-transform:uppercase}
.account{right:100px;top:23px;font-size:8.5px;font-weight:700;color:var(--white);word-spacing:2px}
.account span{margin:0 10px}

.main-nav{left:100px;top:96px;display:flex;gap:28px;font-size:9.6px;color:#555;text-transform:uppercase}
.main-nav .active{color:var(--blue-dark);font-weight:700}
.search{left:607px;top:86px;width:151px;height:23px;border:1px solid #d8d8d8;font-size:8px;color:#888;padding:7px 10px}
.search svg{position:absolute;right:8px;top:4px}

.hero{left:0;top:133px;width:859px;height:382px;
  background:radial-gradient(circle at 430px 210px,#3a6aa6 0,#2b4a78 90px,#59606e 200px,#4a4f5a 430px);}
.hero-title{left:0;width:859px;text-align:center;color:var(--white);font-weight:700}
.hero-title.big{top:132px;font-size:39px}
.hero-title.sub{top:180px;font-size:26px}
.hero .arrow{top:176px}

.features{left:101px;top:453px;width:657px;height:200px;background:var(--white)}
.feature{position:absolute;top:0;width:200px;text-align:center}
.feature svg{display:block;margin:22px auto 0}
.feature h3{font-size:13px;color:var(--ink);font-weight:700;margin-top:14px;text-transform:uppercase}
.feature p{font-size:8.4px;line-height:16px;margin-top:10px}
.btn{display:inline-block;margin-top:12px;background:var(--blue);color:var(--white);font-size:8.5px;padding:6px 9px}

.rule{height:1px;background:var(--rule)}
.pager{left:412px;top:667px;display:flex;gap:3px}

.section-title{left:0;width:859px;text-align:center;font-size:18px;font-weight:700;color:var(--ink);text-transform:uppercase}
.section-title em{font-style:normal;color:var(--blue)}
.welcome{left:135px;top:741px;width:590px;text-align:center;font-size:8.4px;line-height:17.5px}

.news{position:absolute;top:891px;width:181px;text-align:center}
.news .photo{width:181px;height:108px;border:1px solid #ccc}
.news .meta{display:flex;justify-content:center;gap:20px;margin-top:14px}
.news .meta span{border:1px solid #ccc;font-size:7.8px;padding:5px 7px;color:#666}
.news .meta .count{display:flex;align-items:center;gap:4px;color:#222}
.news p{font-size:8.3px;line-height:16px;margin-top:9px}

.site-footer{left:0;top:1122px;width:859px;height:78px;background:var(--footer)}
.footer-links{left:121px;top:22px;font-size:8.3px;color:var(--white)}
.footer-links span{margin:0 7px}
.copyright{left:121px;top:42px;font-size:8.3px;color:var(--white)}
.social{left:610px;top:28px;display:flex;gap:8px}
.social i{display:block;width:20px;height:20px;border-radius:50%;background:#2a2a2a}
</style>
</head>
<body>

<header class="abs site-header">
  <div class="abs top-edge"></div>
  <div class="abs tag-band"></div>
  <div class="abs brand">KSR</div>
  <div class="abs tagline">Kellwyn Surface Records</div>
  <div class="abs account">LOGIN<span>|</span>DEMO LOGIN</div>
</header>

<nav class="abs main-nav">
  <span class="active">Home</span><span>Products</span><span>Reports</span><span>Benefits</span><span>Logislation</span><span>Contact Us</span>
</nav>
<div class="abs search">Search
  <svg width="14" height="14" viewBox="0 0 14 14"><circle cx="6" cy="6" r="4.2" fill="none" stroke="#999" stroke-width="1.2"/><line x1="9" y1="9" x2="13" y2="13" stroke="#999" stroke-width="1.4"/></svg>
</div>

<section class="abs hero" role="img" aria-label="Globe surrounded by devices and connected user icons over data charts">
  <div class="abs hero-title big">HELPING</div>
  <div class="abs hero-title sub">YOU CLEAN UP YOUR COMMUNITY</div>
  <svg class="abs arrow" style="left:82px" width="18" height="30" viewBox="0 0 18 30"><polyline points="15,2 3,15 15,28" fill="none" stroke="#fff" stroke-width="3"/></svg>
  <svg class="abs arrow" style="left:760px" width="18" height="30" viewBox="0 0 18 30"><polyline points="3,2 15,15 3,28" fill="none" stroke="#fff" stroke-width="3"/></svg>
</section>

<section class="abs features">
  <div class="feature" style="left:29px">
    <svg width="26" height="34" viewBox="0 0 26 34"><path d="M2 1h16l6 6v26H2z" fill="none" stroke="#3f9fd6" stroke-width="2"/><text x="13" y="17" font-size="13" font-weight="700" fill="#3f9fd6" text-anchor="middle" font-family="Carlito,sans-serif">$</text><g stroke="#3f9fd6" stroke-width="1.5"><line x1="7" y1="22" x2="19" y2="22"/><line x1="7" y1="26" x2="19" y2="26"/><line x1="7" y1="30" x2="19" y2="30"/></g></svg>
    <h3>Graffiti Register</h3>
    <p>KSR provides a National Register of Vandalism and Graffiti. Subscribers to the KSR Database can Add, Change, Report on and Archive their own Graffiti Jobs.</p>
    <span class="btn">More Info</span>
  </div>
  <div class="feature" style="left:229px">
    <svg width="34" height="34" viewBox="0 0 34 34"><rect x="0" y="0" width="34" height="34" fill="#3f9fd6"/><rect x="4" y="4" width="26" height="26" fill="#fff"/><polygon points="4,30 16,16 22,23 26,19 30,24 30,30" fill="#3f9fd6"/><circle cx="24" cy="10" r="3" fill="#3f9fd6"/></svg>
    <h3>Graffiti Photos</h3>
    <p>KSR allows its subscribers to add Digital Pho-tographs to the Graffiti Jobs. Cleaner Photo-graphs can also be Added as a record of Job Completion.</p>
    <span class="btn">More Info</span>
  </div>
  <div class="feature" style="left:427px">
    <svg width="34" height="30" viewBox="0 0 34 30"><rect x="4" y="0" width="26" height="4" fill="#3f9fd6"/><rect x="2" y="6" width="30" height="4" fill="#3f9fd6"/><rect x="0" y="12" width="34" height="18" rx="2" fill="#3f9fd6"/><rect x="12" y="17" width="10" height="4" fill="#fff"/></svg>
    <h3>Graffiti Archive</h3>
    <p>KSR will hold secure the commercial and sensitive details of your Graffiti. However the statistical and photographic records will be shared between all subscribers.</p>
    <span class="btn">More Info</span>
  </div>
</section>

<div class="abs rule" style="left:168px;top:675px;width:232px"></div>
<div class="abs rule" style="left:460px;top:675px;width:231px"></div>
<div class="abs pager">
  <svg width="16" height="16" viewBox="0 0 16 16"><circle cx="8" cy="8" r="8" fill="#c8c8c8"/><polyline points="9.5,4 5.5,8 9.5,12" fill="none" stroke="#fff" stroke-width="1.8"/></svg>
  <svg width="16" height="16" viewBox="0 0 16 16"><circle cx="8" cy="8" r="8" fill="#777"/><polyline points="6.5,4 10.5,8 6.5,12" fill="none" stroke="#fff" stroke-width="1.8"/></svg>
</div>

<h2 class="abs section-title" style="top:703px">Welcome to <em>KSR</em></h2>
<p class="abs welcome">KSR is an Online Database System to Manage Graffiti in your area or Your Properties KSR allows you to Register, Track, Report and Archive Graffiti Jobs with Photographic Records. KSR records both Estimated and Actual hours and costs for each job, enabling you to track the effectiveness of Anti Graffiti policy. KSR allows sharing of Critical Graffiti Tag and Photographic Data between its subscribers, assisting with tracking down Serial Graffiti Offenders. KSR has a Statistical and Comparison Reporting Systems to allow its subscribers to graphically report and compare their Graffiti Data.</p>

<div class="abs rule" style="left:168px;top:827px;width:523px"></div>
<h2 class="abs section-title" style="top:848px">Latest <em>News</em></h2>

<article class="news" style="left:121px">
  <div class="photo" role="img" aria-label="Hands using a smartphone over a laptop" style="background:linear-gradient(135deg,#3a2a24,#8a6a58 50%,#2a2020)"></div>
  <div class="meta"><span>NOVEMBER 04, 2014</span><span class="count"><svg width="12" height="9" viewBox="0 0 12 9"><ellipse cx="6" cy="4" rx="6" ry="4" fill="#3f9fd6"/><polygon points="2,6 1,9 5,7" fill="#3f9fd6"/></svg>2</span></div>
  <p>Companies have a variety of needs and poten-tial problems. Recognizing your risks and taking measures to protect your</p>
</article>
<article class="news" style="left:339px">
  <div class="photo" role="img" aria-label="Hands touching a transparent screen of business charts" style="background:linear-gradient(135deg,#b8d6ee,#5f95c6 55%,#d2e4f2)"></div>
  <div class="meta"><span>NOVEMBER 04, 2014</span><span class="count"><svg width="12" height="9" viewBox="0 0 12 9"><ellipse cx="6" cy="4" rx="6" ry="4" fill="#3f9fd6"/><polygon points="2,6 1,9 5,7" fill="#3f9fd6"/></svg>2</span></div>
  <p>Companies have a variety of needs and poten-tial problems. Recognizing your risks and taking measures to protect your</p>
</article>
<article class="news" style="left:561px">
  <div class="photo" role="img" aria-label="Business people reviewing charts on a tablet" style="background:linear-gradient(135deg,#1f3550,#5a7fa6 55%,#c9d8e6)"></div>
  <div class="meta"><span>NOVEMBER 04, 2014</span><span class="count"><svg width="12" height="9" viewBox="0 0 12 9"><ellipse cx="6" cy="4" rx="6" ry="4" fill="#3f9fd6"/><polygon points="2,6 1,9 5,7" fill="#3f9fd6"/></svg>2</span></div>
  <p>Companies have a variety of needs and poten-tial problems. Recognizing your risks and taking measures to protect your</p>
</article>

<footer class="abs site-footer">
  <div class="abs footer-links">Home<span>|</span>Products<span>|</span>Reports<span>|</span>Benefits<span>|</span>Logislation<span>|</span>Contact Us</div>
  <div class="abs copyright">Copyright © 2014 ksr. All Rights Reserved</div>
  <div class="abs social"><i></i><i></i><i></i><i></i><i></i></div>
</footer>

</body>
</html>
```